Local Flower Farm Needs Business Card Design

I need business cards designed for a flower farm based in Eudora, Kansas.
Business Info:
We are a local cut flower farm located in Eudora, Kansas, founded by Corinne Haldwick. What started as a passion for agriculture and search for more joy in daily life has blossomed into a small business dedicated to providing the community with beautiful, fresh, and sustainable flowers. We specialize in local, seasonal blooms, ensuring that every petal reflects the care and dedication we pour into our craft. Our mission is to deliver the highest quality flowers directly to our customers through local farmers markets and to florists who share our commitment to sustainability. Join us in celebrating the beauty of nature, one bloom at a time!
Contact Details:
Corinne Haldwick
Owner
Phone 913-555-0147
Facebook: Rosalind Thorpe Gardens
Instagram: @RosalindThorpeGardens
Website: RosalindThorpeGardens.example
Target Market(s)
Wholesale to Florists and Direct to Consumer via Farmers Market
Industry/Entity Type
Florist, Farm
Contact Information for Business Card
Name, Contact Info, Logo
Look and feel
Each slider illustrates characteristics of the customer's brand and the style your logo design should communicate.

```html
<!DOCTYPE html>
<html lang="en">
<head>
<meta charset="utf-8">
<title>Rosalind Thorpe Gardens – Business Card</title>
<link href="https://fonts.googleapis.com/css2?family=Tinos:wght@400;700&display=swap" rel="stylesheet">
<style>
  :root {
    --backdrop: #e3e7e8;
    --card: #0a2730;
    --ink: #f2f2f2;
    --sage: #8ccf9c;
    --line: #dfe6e6;
  }
  * { box-sizing: border-box; margin: 0; padding: 0; }
  html, body {
    width: 1200px; height: 960px; overflow: hidden;
    background: var(--backdrop);
    font-family: "Tinos", "Times New Roman", serif;
  }
  .card {
    position: absolute; left: 215px;
    width: 702px; height: 400px;
    background: var(--card);
    border-radius: 30px;
    overflow: hidden;
    color: var(--ink);
  }
  .card--front { top: 60px; }
  .card--back { top: 500px; }

  .brand-seal {
    position: absolute;
    border: 1px solid var(--line);
    border-radius: 50%;
    display: flex; align-items: center; justify-content: center;
    text-align: center;
  }
  .brand-seal__name {
    font-weight: 400;
    text-transform: uppercase;
    color: var(--ink);
    line-height: 1.35;
  }
  .card--front .brand-seal { left: 224px; top: 74px; width: 252px; height: 252px; }
  .card--front .brand-seal__name { font-size: 22px; letter-spacing: 4px; }
  .card--back .brand-seal { left: 27px; top: 27px; width: 180px; height: 180px; }
  .card--back .brand-seal__name { font-size: 16px; letter-spacing: 3px; }

  .owner {
    position: absolute; right: 30px; top: 28px;
    text-align: right;
  }
  .owner__name { font-size: 33px; font-weight: 700; letter-spacing: 1.5px; line-height: 1; }
  .owner__role { font-size: 16px; letter-spacing: 0.5px; margin-top: 4px; }
  .owner-tab {
    position: absolute; right: 0; top: 31px;
    width: 20px; height: 60px; background: var(--ink);
  }

  .contacts {
    position: absolute; left: 24px; top: 283px;
    list-style: none;
  }
  .contacts li {
    display: flex; align-items: center;
    height: 24px;
    font-size: 17px; letter-spacing: 0.6px;
  }
  .contacts svg { width: 18px; height: 18px; margin-right: 10px; flex: none; }

  .brand-mark-large {
    position: absolute; right: 14px; bottom: 16px;
    width: 200px;
    text-align: right;
    color: var(--sage);
    opacity: 0.8;
    font-size: 34px; font-weight: 700;
    line-height: 1.05;
  }
</style>
</head>
<body>

<section class="card card--front">
  <div class="brand-seal">
    <p class="brand-seal__name">Rosalind<br>Thorpe<br>Gardens</p>
  </div>
</section>

<section class="card card--back">
  <div class="brand-seal">
    <p class="brand-seal__name">Rosalind<br>Thorpe<br>Gardens</p>
  </div>

  <div class="owner">
    <p class="owner__name">Corinne Haldwick</p>
    <p class="owner__role">Owner</p>
  </div>
  <div class="owner-tab"></div>

  <ul class="contacts">
    <li>
      <svg viewBox="0 0 24 24" aria-hidden="true"><path fill="var(--ink)" d="M6.6 10.8a15.1 15.1 0 0 0 6.6 6.6l2.2-2.2c.3-.3.7-.4 1-.2 1.1.4 2.3.6 3.6.6.6 0 1 .4 1 1V20c0 .6-.4 1-1 1A17 17 0 0 1 3 4c0-.6.4-1 1-1h3.5c.6 0 1 .4 1 1 0 1.3.2 2.5.6 3.6.1.3 0 .7-.2 1z"/></svg>
      913-555-0147
    </li>
    <li>
      <svg viewBox="0 0 24 24" aria-hidden="true"><circle cx="12" cy="12" r="10" fill="var(--ink)"/></svg>
      Rosalind Thorpe Gardens
    </li>
    <li>
      <svg viewBox="0 0 24 24" aria-hidden="true"><rect x="3" y="3" width="18" height="18" rx="5" fill="none" stroke="var(--ink)" stroke-width="2"/></svg>
      @RosalindThorpeGardens
    </li>
    <li>
      <svg viewBox="0 0 24 24" aria-hidden="true"><circle cx="12" cy="12" r="9" fill="none" stroke="var(--ink)" stroke-width="2"/><ellipse cx="12" cy="12" rx="4" ry="9" fill="none" stroke="var(--ink)" stroke-width="1.5"/><line x1="3" y1="12" x2="21" y2="12" stroke="var(--ink)" stroke-width="1.5"/></svg>
      RosalindThorpeGardens.example
    </li>
  </ul>

  <p class="brand-mark-large">Rosalind<br>Thorpe<br>Gardens</p>
</section>

</body>
</html>
```